Website development company website

ABOUT COMPANY
Hi everyone! We're a Melbourne, Australia website development company in a need of a website design that will make online store merchants want to engage our services.
We specialise exclusively in Torvista e-commerce platform (https://torvista-platform.example/). What distinguishes our business from competition is that rather than designing and building brand new websites, we offer development, support and maintenance services to established websites. Maintenance and Support are the keywords representing our business.
Our potential clients are people with broken, slow and underperforming Torvista installations who need assistance getting their websites up and making sales. Our website must pass the message that we can help, and provide quick means of making contact.
DESIGN
Overall, we're looking for a slick, clean, airy, conservative design. No need to do anything crazy, try to stick to what's "standard" in website design these days and make it easy on all of us. The website is unlikely to be updated too often so it needs to look attractive and fresh first time over and after a year, too.
Attached is our new logo, which you'll be able to take the basic idea from, the colors and fonts. Though, don't use the fonts from the logo in the website, stick to the standard widely supported fonts. Additional use of Google fonts is fine.
Don't overdo it with colors, stick to conservative basic color set and only use the colors from the log for accents like headings etc. Please, don't be tempted to use the blue and orange as background of whole blocks, other than perhaps footer. Thanks.
For the images used, I'd like to stay away from a design studio/digital agency feel and lean more towards professional support and maintenance services. I'm thinking images of content merchants doing their job. Something along the lines of "We'll be taking care of the website so that you only need to care about the business".
Some ideas I like:
http://www.plumframe-pics.example/detail/photo/portrait-of-confident-male-design-professional-royalty-free-image/572048163
http://www.plumframe-pics.example/detail/photo/designer-taking-picture-of-hat-high-res-stock-photography/839207514
http://www.plumframe-pics.example/detail/photo/woman-packaging-pottery-royalty-free-image/216684093
Images of colorful shopping bags and shopping carts are over the top and not serious enough. Instead of images matching Online Shopping, I'd try going more for Stability, Reliability, Performance.
Our existing website is http://www.bravuln.example. Please, don't take design ideas from it, but it will give you a picture of the structure of our new website and content that's going to be used initially.
If you could include a basic icon set to use throughout the website, that would be great. If the icons could match our logo (attached), it would be a big plus.
ALL PAGES
Every page must contain clearly visible phone number (1300 648 907) and a Contact Us Now button, which opens an AJAX driven popup form with Name, Email, Phone and Message to be sent through.
To start with, main menu items will be Torvista, Portfolio, Contact.
At the bottom of each page, please, include a newsletter subscription form with text Subscribe to Torvista Support and Security Updates.
For the footer, I'd like to see a logo strip with the following logos in grayscale (no need to link anywhere): Torvista, QRX, DataVane, NCB. You'll find the logos on Google Images.
Standard footer columns follow. Here, I'd like to see logos in color: Torvista Certified Developer, Torvista Ceritified Solution Provider. Again, the logos are on Google Images.
No social media logos/links necessary anywhere on the website.
...and then the copyright line.
FRONT PAGE
Large slider with images that would appeal to our target audience. Keywords here would be Torvista System Audit, Torvista Performance Optimisation, Torvista Website Emergency Recovery, Torvista Development Infrastructure Hosting. We'll have a static page created for each of these to link to.
In a corner of the slider, or on the edge, can I have an overlay with logos in color (same as footer): Torvista Certified Developer, Torvista Ceritified Solution Provider.
Underneath, a number of blocks, each with an image and teaser that we'll use to link to various pages throughout the website.
PORTFOLIO PAGE
I'm thinking a single long page with a block per client, which will contain project name, description from us and a testimonial from client. Also, each block will contain a single large screenshot. No gallery or slideshow is necessary here, just one image per project.
I'll leave the layout up to you, but try to put yourself in the shoes of a potential client reviewing our past work by simply scrolling down this one page.
CONTACT US PAGE
Separate page with the same form as above, phone number (1300 648 907), email address (support@kavreo.example), address (Suite 42, Level 3|8 Wattlebrook Lane|Fernvale Heights VIC 3999), and a grayscale Google Map.
CODING UP
Coding up into static HTML/CSS/JS is equally important as the design itself. We're a website development company, we'll be integrating the theme. We will spot any issues and we will point them out.
Coded up design must be fully responsive. Enough said.
To be able to create any content in future, we'd like one extra page coded up with samples of all themed elements, lists, forms, buttons, 2, 3, 4-column layout, alerts, icons, etc. This page does not need to be designed, only coded up.
The design will be integrated into Drupal using Twig. If possible at all, try to keep it in mind when designing and coding up, and make the integration into a Drupal theme easier for us.
GOOD LUCK!
That's it. Let me know if anything needs clarifying. So far I've had a great experience with ArtFlockly. I don't doubt some great designs will emerge. Clever ideas are highly appreciated, but also make it clear you've read and followed the points in this brief. Cheers, Tom

```html
<!DOCTYPE html>
<html lang="en">
<head>
<meta charset="utf-8">
<title>Kavreo E-commerce</title>
<link href="https://fonts.googleapis.com/css2?family=Open+Sans:wght@400;600&family=Raleway:wght@300;400;500;600&display=swap" rel="stylesheet">
<style>
:root{
  --orange:#e8801f;
  --navy:#0d3a6e;
  --footer:#083a72;
  --footer-input:#0f4f95;
  --grey-bg:#ececec;
  --strip-bg:#e6e6e6;
  --text:#6b6b6b;
  --line:#d6d6d6;
  --white:#ffffff;
}
*{box-sizing:border-box;margin:0;padding:0}
html,body{width:1200px;height:3291px;overflow:hidden}
body{background:var(--white);font-family:"Open Sans",Arial,sans-serif;color:var(--text);position:relative}
.section{position:absolute;left:0;width:1200px}
.abs{position:absolute}
.heading{font-family:"Raleway",Arial,sans-serif;font-weight:400;font-size:40px;color:var(--navy);letter-spacing:1px;text-transform:uppercase}
.heading .accent{color:var(--orange)}
.btn{display:inline-flex;align-items:center;justify-content:center;background:var(--orange);color:var(--white);font-family:"Open Sans",Arial,sans-serif;font-size:20px;text-transform:uppercase;letter-spacing:.5px;text-decoration:none}
p.body{font-size:14.5px;line-height:25px;color:var(--text)}

/* header */
.site-header{top:0;height:156px;background:var(--white)}
.topbar{right:77px;top:8px;display:flex;align-items:center;gap:10px;font-size:15px}
.topbar .help{color:var(--orange);text-transform:uppercase;letter-spacing:.3px}
.topbar .phone{color:var(--navy);font-weight:600;font-size:17px}
.topbar-line{left:77px;right:77px;top:44px;height:1px;background:var(--line)}
.brand{left:77px;top:66px;display:flex;align-items:center;gap:12px;text-decoration:none}
.brand-square{width:56px;height:64px;background:var(--navy)}
.brand-name{font-family:"Raleway",Arial,sans-serif;font-weight:600;font-size:44px;line-height:44px;color:var(--navy)}
.brand-name small{display:block;font-size:14px;line-height:16px;letter-spacing:3px}
.main-nav{right:77px;top:80px;display:flex;gap:46px}
.main-nav a{font-family:"Open Sans",Arial,sans-serif;font-size:17px;color:#555;text-decoration:none;text-transform:uppercase;padding-bottom:6px}
.main-nav a.active{color:var(--navy);border-bottom:2px solid var(--navy)}

/* hero */
.hero{top:156px;height:625px;background:linear-gradient(90deg,#efe8e0 0%,#f4f3f2 35%,#d4d7dc 70%,#9ea6b1 100%)}
.hero-caption{left:220px;width:760px;top:208px;text-align:center;font-family:"Raleway",Arial,sans-serif;font-size:31px;line-height:52px;color:var(--navy);text-transform:uppercase;font-weight:500}
.hero .btn{position:absolute;left:469px;top:388px;width:260px;height:62px;font-size:22px}

/* who we are */
.who{top:781px;height:364px;background:var(--grey-bg)}
.who .heading{left:77px;top:58px}
.who-text{left:77px;top:118px;width:510px}
.who-text p+p{margin-top:24px}
.monitor{left:706px;top:53px;width:417px;height:311px;background:linear-gradient(180deg,#2a2a2a 0%,#3b3b3b 75%,#c9c9c9 76%,#e2e2e2 100%)}

/* key values */
.values{top:1145px;height:490px;background:var(--white)}
.values .heading{left:0;width:1200px;top:86px;text-align:center}
.value{top:158px;width:340px;text-align:center}
.value-icon{width:124px;height:124px;border:1px solid #cfcfcf;border-radius:50%;margin:0 auto;display:flex;align-items:center;justify-content:center}
.value h3{margin-top:28px;font-family:"Raleway",Arial,sans-serif;font-weight:400;font-size:25px;color:var(--navy);text-transform:uppercase;letter-spacing:.5px}
.value p{margin-top:14px;font-size:14.5px;line-height:24px;color:var(--text)}

/* banner */
.banner{top:1635px;height:416px;background:linear-gradient(90deg,#c9a087 0%,#d8cfc7 35%,#e6e8e6 60%,#c9d3c2 100%)}
.banner-text{right:77px;top:134px;width:500px;text-align:right;font-family:"Raleway",Arial,sans-serif;font-size:27px;line-height:46px;color:var(--navy)}

/* why */
.why{top:2051px;height:334px;background:var(--grey-bg)}
.why-col{top:58px;width:480px}
.why-col h2{font-family:"Raleway",Arial,sans-serif;font-weight:400;font-size:29px;color:var(--navy);text-transform:uppercase;letter-spacing:.5px}
.why-body{position:relative;margin-top:28px;height:190px}
.why-mark{position:absolute;left:0;top:18px;width:110px;display:flex;flex-direction:column;align-items:center;gap:8px}
.why-mark .sq{width:74px;height:90px;background:var(--navy)}
.why-mark .sq.orange{width:62px;height:62px;background:var(--orange)}
.why-mark span{font-family:"Open Sans",Arial,sans-serif;font-size:20px;color:#333}
.why-divider{position:absolute;left:148px;top:0;width:1px;height:170px;background:#cfcfcf}
.why-copy{position:absolute;left:175px;top:0;width:305px}
.why-copy .btn{margin-top:22px;width:182px;height:48px;font-size:19px}

/* work */
.work{top:2385px;height:467px;background:var(--white)}
.work .heading{left:0;width:1200px;top:50px;text-align:center}
.project{top:118px;width:235px}
.project-logo{height:134px;border:1px solid #d3d3d3;display:flex;align-items:center;justify-content:center;font-family:"Open Sans",Arial,sans-serif;font-size:26px;font-weight:600;color:#333}
.project h3{margin-top:12px;font-family:"Open Sans",Arial,sans-serif;font-weight:400;font-size:19px;color:var(--navy)}
.project p{margin-top:4px;font-size:13.5px;line-height:22px;color:var(--text)}
.project .by{margin-top:2px;font-size:13.5px;color:var(--orange)}

/* partner strip */
.partners{top:2852px;height:123px;background:var(--strip-bg);display:flex;justify-content:space-around;align-items:center;padding:0 77px}
.partner{font-family:"Open Sans",Arial,sans-serif;font-size:34px;color:#8a8a8a;display:flex;align-items:center;gap:12px}
.partner .sq{width:36px;height:36px;background:#9a9a9a}

/* footer */
.site-footer{top:2975px;height:316px;background:var(--footer);color:var(--white)}
.footer-col{top:38px}
.footer-col h4{font-family:"Raleway",Arial,sans-serif;font-weight:400;font-size:20px;color:var(--orange);letter-spacing:.5px}
.links{list-style:none;margin-top:14px}
.links li{font-size:15px;line-height:31px}
.links li a{color:var(--white);text-decoration:none}
.links li a.current{color:var(--orange)}
.newsletter p{margin-top:18px;font-size:15px;line-height:25px;width:310px}
.newsletter .field{margin-top:12px;width:312px;height:40px;background:var(--footer-input);border:1px solid #2d6db2;color:var(--white);font-size:15px;padding:0 10px;display:flex;align-items:center}
.newsletter .btn{margin-top:14px;width:165px;height:40px;font-size:19px}
.contact-list{list-style:none;margin-top:16px}
.contact-list li{display:flex;gap:14px;font-size:15px;line-height:25px;margin-bottom:12px}
.contact-list li .ic{width:18px;flex:none;padding-top:4px}
.contact-list a{color:var(--orange);text-decoration:underline}
.footer-line{left:77px;right:77px;top:265px;height:1px;background:#2c5a8f}
.copyright{left:0;width:1200px;top:282px;text-align:center;font-size:14px}
.copyright b{color:var(--orange);font-weight:600}
</style>
</head>
<body>

<header class="section site-header">
  <div class="abs topbar">
    <span class="help">We can help you</span>
    <svg width="18" height="18" viewBox="0 0 24 24"><path fill="#0d3a6e" d="M6.6 10.8a15.1 15.1 0 0 0 6.6 6.6l2.2-2.2c.3-.3.7-.4 1-.2 1.1.4 2.3.6 3.6.6.6 0 1 .4 1 1V20c0 .6-.4 1-1 1A17 17 0 0 1 3 4c0-.6.4-1 1-1h3.5c.6 0 1 .4 1 1 0 1.3.2 2.5.6 3.6.1.3 0 .7-.2 1z"/></svg>
    <span class="phone">1300 648 907</span>
  </div>
  <div class="abs topbar-line"></div>
  <a class="abs brand" href="#">
    <span class="brand-square"></span>
    <span class="brand-name">Kavreo<small>E-COMMERCE</small></span>
  </a>
  <nav class="abs main-nav">
    <a class="active" href="#">Home</a>
    <a href="#">About</a>
    <a href="#">Torvista</a>
    <a href="#">Portfolio</a>
    <a href="#">Contact</a>
  </nav>
</header>

<section class="section hero" role="img" aria-label="Smiling merchant in glasses at her desk in front of a screen full of product photos">
  <h1 class="abs hero-caption">We will be taking care of the website so that you only need to care about the business</h1>
  <a class="btn" href="#">Contact us now</a>
</section>

<section class="section who">
  <h2 class="abs heading"><span class="accent">Who</span> we are</h2>
  <div class="abs who-text">
    <p class="body">Lorem Ipsum is simply dummy text of the printing and typesetting industry. Lorem Ipsum has been the industry's standard dummy text ever since the 1500s, when an unknown printer took a galley of type and scrambled it to make a type specimen book.</p>
    <p class="body">Lorem Ipsum is simply dummy text of the printing and typesetting industry. Lorem Ipsum has been the industry's standard dummy text ever since the 1500</p>
  </div>
  <div class="abs monitor" role="img" aria-label="Desktop monitor displaying the Kavreo E-commerce name"></div>
</section>

<section class="section values">
  <h2 class="abs heading"><span class="accent">Key</span> values</h2>
  <div class="abs value" style="left:63px">
    <div class="value-icon">
      <svg width="50" height="40" viewBox="0 0 50 40" fill="none" stroke="#e8801f" stroke-width="5" stroke-linecap="round" stroke-linejoin="round"><path d="M15 6 3 20l12 14M35 6l12 14-12 14M29 3 21 37"/></svg>
    </div>
    <h3>Development</h3>
    <p>Lorem Ipsum is simply dummy text of the printing and typesetting industry. Lorem Ipsum has been the industry.</p>
  </div>
  <div class="abs value" style="left:430px">
    <div class="value-icon">
      <svg width="48" height="44" viewBox="0 0 48 44"><circle cx="24" cy="13" r="11" fill="#e8801f"/><path d="M4 44c0-12 9-19 20-19s20 7 20 19z" fill="#e8801f"/></svg>
    </div>
    <h3>Support</h3>
    <p>Lorem Ipsum is simply dummy text of the printing and typesetting industry. Lorem Ipsum has been the industry.</p>
  </div>
  <div class="abs value" style="left:796px">
    <div class="value-icon">
      <svg width="52" height="48" viewBox="0 0 52 48"><circle cx="20" cy="28" r="12" fill="none" stroke="#e8801f" stroke-width="7" stroke-dasharray="5 4"/><circle cx="20" cy="28" r="4" fill="#e8801f"/><circle cx="39" cy="12" r="7" fill="none" stroke="#e8801f" stroke-width="5" stroke-dasharray="3.5 2.5"/></svg>
    </div>
    <h3>Maintenance</h3>
    <p>Lorem Ipsum is simply dummy text of the printing and typesetting industry. Lorem Ipsum has been the industry.</p>
  </div>
</section>

<section class="section banner" role="img" aria-label="Hand holding a smartphone showing a shopping list app">
  <p class="abs banner-text">Lorem Ipsum is simply dummy text of the printing and types industry. Lorem Ipsum has been the industry.</p>
</section>

<section class="section why">
  <div class="abs why-col" style="left:77px">
    <h2>Why Kavreo E-commerce ?</h2>
    <div class="why-body">
      <div class="why-mark"><span class="sq"></span></div>
      <div class="why-divider"></div>
      <div class="why-copy">
        <p class="body">Lorem Ipsum is simply dummy text of the printing and typesetting industry. Lorem Ipsum has been the industry's standard dummy text ever since the 1500.</p>
        <a class="btn" href="#">Contact us</a>
      </div>
    </div>
  </div>
  <div class="abs why-col" style="left:652px">
    <h2>Why Torvista ?</h2>
    <div class="why-body">
      <div class="why-mark"><span class="sq orange"></span><span>Torvista</span></div>
      <div class="why-divider"></div>
      <div class="why-copy">
        <p class="body">Lorem Ipsum is simply dummy text of the printing and typesetting industry. Lorem Ipsum has been the industry's standard dummy text ever since the 1500.</p>
        <a class="btn" href="#">Read more</a>
      </div>
    </div>
  </div>
</section>

<section class="section work">
  <h2 class="abs heading"><span class="accent">Our</span> work</h2>
  <article class="abs project" style="left:77px">
    <div class="project-logo">Stackwell Goods</div>
    <h3>Stackwell Goods</h3>
    <p>Bravuln are prompt and get the job done with the highest level of workmanship at a resonable price.</p>
    <p class="by">Carl Hemsworthy, Stackwell Goods</p>
  </article>
  <article class="abs project" style="left:349px">
    <div class="project-logo">Norvik</div>
    <h3>Norvik</h3>
    <p>A fast solution is key when you are selling online. Bravuln are now our go to Torvista developers, very happy.</p>
    <p class="by">Piet Van Droom, Norvik</p>
  </article>
  <article class="abs project" style="left:619px">
    <div class="project-logo">Lumira</div>
    <h3>Lumira</h3>
    <p>Bravuln went above and beyond by delivering great work in excellent time frames.</p>
    <p class="by">Reggie Tallow, Lumira</p>
  </article>
  <article class="abs project" style="left:891px">
    <div class="project-logo">Velline</div>
    <h3>Velline</h3>
    <p>Bravuln are great developers whose concentration on detail does not compromise the delivery of work.</p>
    <p class="by">Morgan Ashby, Velline</p>
  </article>
</section>

<section class="section partners">
  <span class="partner"><span class="sq"></span>Torvista</span>
  <span class="partner">DataVane</span>
  <span class="partner">QRX</span>
  <span class="partner">NCB</span>
</section>

<footer class="section site-footer">
  <div class="abs footer-col" style="left:77px">
    <h4>Useful Links</h4>
    <ul class="links">
      <li><a class="current" href="#">Home</a></li>
      <li><a href="#">About</a></li>
      <li><a href="#">Torvista</a></li>
      <li><a href="#">Portfolio</a></li>
      <li><a href="#">Contact</a></li>
    </ul>
  </div>
  <div class="abs footer-col newsletter" style="left:445px">
    <h4>Newsletter</h4>
    <p>Subscribe to Torvista Support and Security Updates</p>
    <div class="field">Enter Email Id</div>
    <a class="btn" href="#">Subscribe</a>
  </div>
  <div class="abs footer-col" style="left:812px">
    <h4>Get In Touch With Us</h4>
    <ul class="contact-list">
      <li>
        <span class="ic"><svg width="14" height="20" viewBox="0 0 14 20"><path fill="#e8801f" d="M7 0a7 7 0 0 0-7 7c0 5 7 13 7 13s7-8 7-13a7 7 0 0 0-7-7zm0 9.5A2.5 2.5 0 1 1 7 4.5a2.5 2.5 0 0 1 0 5z"/></svg></span>
        <span>Suite 42, Level 3, Harbourline Building<br>8 Wattlebrook Lane<br>Fernvale Heights VIC 3999<br><a href="#">VIEW MAP</a></span>
      </li>
      <li>
        <span class="ic"><svg width="16" height="16" viewBox="0 0 24 24"><path fill="#e8801f" d="M6.6 10.8a15.1 15.1 0 0 0 6.6 6.6l2.2-2.2c.3-.3.7-.4 1-.2 1.1.4 2.3.6 3.6.6.6 0 1 .4 1 1V20c0 .6-.4 1-1 1A17 17 0 0 1 3 4c0-.6.4-1 1-1h3.5c.6 0 1 .4 1 1 0 1.3.2 2.5.6 3.6.1.3 0 .7-.2 1z"/></svg></span>
        <span style="font-weight:600">1300 648 907</span>
      </li>
      <li>
        <span class="ic"><svg width="17" height="13" viewBox="0 0 17 13" fill="none" stroke="#e8801f" stroke-width="1.6"><rect x="1" y="1" width="15" height="11"/><path d="m1 1 7.5 6L16 1"/></svg></span>
        <span>info@kavreo.example</span>
      </li>
    </ul>
  </div>
  <div class="abs footer-line"></div>
  <p class="abs copyright">© <b>Kavreo E-commerce</b> - 2016. All Rights Reserved.</p>
</footer>

</body>
</html>
```